Health and Wellness company needs flyer to promote free seminar

Corvella Motion studio is a health and wellness company that offers an exercise program designed by physical therapists to help relieve pain and improve mobility. Our business is a new concept that is not well understood by the public. In order to promote our business we offer a free seminar where we present information regarding the underlying cause of pain and tightness. During the seminar we also perform a posture screen and movement testing for all participants.

Target Market(s)

Mostly healthy and active women ages 25-65

Industry/Entity Type

Health And Wellness

Font styles to use
Sans Serif

Colors

Designer to choose colors to be used in the design.

Requirements
Must have
• Title: Eliminate Pain and Tightness For Good
• Paragraph: Corvella Motion Studio offers a free 60 minute seminar: "The Busy Walker's Manual for Stretching and Living Lighter."
• What to Expect:
• • Identify the underlying cause of your pain and mobility issues
• • Expose what gets in the way of you moving and feeling better
• • Learn why traditional exercises don’t help and can actually make the problem worse
• • Reveal what your posture is saying and how that impacts you
• • Experience your muscle imbalances through movement tests
• • Discover the training method that realigns your posture, increases your mobility and reduces your pain
• Call to action: RSVP online at corvellamotionstudio.com
Nice to have
• Use a relevant image showing a female dealing with tightness in the low back, legs, etc.
• Emphasize that the seminar is FREE.
• Make the call to action prominent.

```html
<!DOCTYPE html>
<html lang="en">
<head>
<meta charset="utf-8">
<title>Free Seminar Flyer – Corvella Motion Studio</title>
<link rel="stylesheet" href="https://fonts.googleapis.com/css2?family=Lato:wght@400;700&family=Oswald:wght@500;600&family=Roboto+Condensed:wght@400;500&family=Ubuntu:wght@400;500&display=swap">
<style>
  :root {
    --stage: #6b6b6b;
    --paper: #ffffff;
    --orange: #f5921e;
    --purple: #4a4f9e;
    --violet: #5a5fb5;
    --ink-purple: #3d1fa8;
    --ink: #2b2b2b;
    --rule: #ffffff;
  }
  * { margin: 0; padding: 0; box-sizing: border-box; }
  html, body { width: 1200px; height: 1200px; overflow: hidden; background: var(--stage); }
  .flyer {
    position: absolute; left: 186px; top: 20px;
    width: 875px; height: 1227px;
    background: var(--paper);
    transform: scale(0.9455); transform-origin: 0 0;
    overflow: hidden;
    font-family: "Lato", sans-serif;
  }
  .flyer-shapes { position: absolute; inset: 0; }
  .abs { position: absolute; }

  .expect-heading { left: 44px; top: 306px; font-family: "Ubuntu", sans-serif; font-weight: 500; line-height: 1; }
  .expect-heading .lead { display: block; color: var(--paper); font-size: 24px; font-family: "Roboto Condensed", sans-serif; }
  .expect-heading .main { display: block; color: var(--purple); font-size: 27px; margin-top: 2px; }

  .expect-item { left: 36px; width: 270px; }
  .expect-item .icon { position: absolute; left: 0; top: 0; width: 32px; height: 32px; }
  .expect-item h3 { margin-left: 41px; font-family: "Ubuntu", sans-serif; font-weight: 400; font-size: 17px; color: var(--purple); line-height: 1.1; }
  .expect-item p { margin-left: 42px; margin-top: 5px; font-size: 10.5px; color: var(--paper); line-height: 1.35; }
  .expect-item .rule { margin-left: 42px; margin-top: 6px; height: 1px; background: var(--rule); }

  .brand { right: 74px; top: 664px; display: flex; align-items: center; gap: 12px; }
  .brand .mark { width: 52px; height: 52px; border: 5px solid var(--purple); }
  .brand .name { font-family: "Lato", sans-serif; font-weight: 700; font-size: 26px; color: var(--purple); }

  .headline { right: 74px; top: 758px; text-align: right; font-family: "Roboto Condensed", sans-serif; font-weight: 400; font-size: 60px; line-height: 60px; color: var(--ink); letter-spacing: -0.5px; }
  .headline .orange { color: var(--orange); }
  .headline .violet { color: var(--ink-purple); }

  .offer { right: 72px; top: 904px; text-align: right; font-size: 21px; color: var(--orange); }
  .guide { right: 72px; top: 938px; text-align: right; font-family: "Roboto Condensed", sans-serif; font-weight: 500; font-size: 19px; color: var(--ink); }

  .cta { right: 72px; text-align: right; }
  .cta .label { font-weight: 700; font-size: 28px; color: var(--ink-purple); line-height: 1.2; }
  .cta .url { font-size: 26px; color: var(--ink); line-height: 1.25; }
  .cta-divider { left: 430px; top: 1088px; width: 372px; height: 1px; background: #8a8a8a; }

  .free { left: 62px; top: 994px; font-family: "Oswald", sans-serif; font-weight: 600; font-size: 96px; line-height: 1; color: var(--orange); }
  .seminar { left: 64px; top: 1100px; font-family: "Oswald", sans-serif; font-weight: 600; font-size: 56px; line-height: 1; color: var(--paper); letter-spacing: 1px; }
</style>
</head>
<body>
<main class="flyer">
  <svg class="flyer-shapes" viewBox="0 0 875 1227" width="875" height="1227" aria-hidden="false">
    <defs>
      <linearGradient id="gymTone" x1="0" y1="0" x2="1" y2="1">
        <stop offset="0" stop-color="#d9dde0"/>
        <stop offset="0.45" stop-color="#6f6a6c"/>
        <stop offset="0.7" stop-color="#b03a6e"/>
        <stop offset="1" stop-color="#2a2628"/>
      </linearGradient>
    </defs>
    <polygon class="panel-orange" points="0,174 458,584 172,866 136,859 0,952" fill="var(--orange)"/>
    <polygon class="panel-purple" points="136,859 0,952 0,1227 454,1227" fill="var(--purple)"/>
    <polygon points="136,859 172,866 160,876" fill="#2f2d7a"/>
    <polygon class="photo-area" role="img" aria-label="Photo: woman in pink sportswear doing a one-arm dumbbell row on a bench in a bright gym"
      points="215,0 875,0 875,352 645,600 615,606 95,150" fill="url(#gymTone)" stroke-linejoin="round"/>
    <polyline class="band-violet" points="176,-20 52,148 560,632" fill="none" stroke="var(--violet)" stroke-width="40" stroke-linejoin="round" stroke-linecap="round"/>
  </svg>

  <h2 class="abs expect-heading"><span class="lead">What to</span><span class="main">Expect</span></h2>

  <div class="abs expect-item" style="top:380px">
    <svg class="icon" viewBox="0 0 32 32"><circle cx="16" cy="16" r="14.5" fill="none" stroke="#fff" stroke-width="1.5"/><circle cx="18" cy="13" r="5" fill="none" stroke="var(--purple)" stroke-width="1.8"/><line x1="14.5" y1="16.5" x2="9" y2="22" stroke="var(--purple)" stroke-width="2.2"/></svg>
    <h3>Identify</h3>
    <p>the underlying cause of your pain<br>and mobility issues</p>
    <div class="rule" style="width:168px"></div>
  </div>

  <div class="abs expect-item" style="top:450px">
    <svg class="icon" viewBox="0 0 32 32"><circle cx="16" cy="16" r="14.5" fill="none" stroke="#fff" stroke-width="1.5"/><path d="M11 14 L16 9 L21 14 M16 9 V19 M10 22 H22" fill="none" stroke="var(--purple)" stroke-width="1.8"/></svg>
    <h3>Expose</h3>
    <p style="margin-top:9px">what gets in the way of you moving<br>and feeling better</p>
    <div class="rule" style="width:198px"></div>
  </div>

  <div class="abs expect-item" style="top:528px">
    <svg class="icon" viewBox="0 0 32 32"><circle cx="16" cy="16" r="14.5" fill="none" stroke="#fff" stroke-width="1.5"/><path d="M8 14 L16 8 L24 14 M10 14 V23 H22 V14 M14 23 V18 H18 V23" fill="none" stroke="var(--purple)" stroke-width="1.6"/></svg>
    <h3>Learn</h3>
    <p>why traditional exercises don't help<br>and can actually make the problem worse</p>
    <div class="rule" style="width:198px"></div>
  </div>

  <div class="abs expect-item" style="top:597px">
    <svg class="icon" viewBox="0 0 32 32"><circle cx="16" cy="16" r="14.5" fill="none" stroke="#fff" stroke-width="1.5"/><rect x="9" y="13" width="14" height="9" rx="2" fill="var(--purple)"/><circle cx="16" cy="10" r="2" fill="var(--purple)"/></svg>
    <h3>Reveal</h3>
    <p style="margin-top:2px">what your posture is saying and how<br>that impacts you</p>
    <div class="rule" style="width:198px"></div>
  </div>

  <div class="abs expect-item" style="top:662px">
    <svg class="icon" viewBox="0 0 32 32"><circle cx="16" cy="16" r="14.5" fill="none" stroke="#fff" stroke-width="1.5"/><rect x="10" y="8" width="12" height="16" fill="none" stroke="var(--purple)" stroke-width="1.6"/><path d="M13 13 H19 M13 16 H19 M13 19 H17" stroke="var(--purple)" stroke-width="1.4"/></svg>
    <h3>Experience</h3>
    <p style="margin-top:8px">your muscle imbalances through<br>movement tests</p>
    <div class="rule" style="width:170px"></div>
  </div>

  <div class="abs expect-item" style="top:734px">
    <svg class="icon" viewBox="0 0 32 32"><circle cx="16" cy="16" r="14.5" fill="none" stroke="#fff" stroke-width="1.5"/><circle cx="11" cy="17" r="4" fill="none" stroke="var(--purple)" stroke-width="1.6"/><circle cx="21" cy="17" r="4" fill="none" stroke="var(--purple)" stroke-width="1.6"/><path d="M15 17 H17" stroke="var(--purple)" stroke-width="1.6"/></svg>
    <h3>Discover</h3>
    <p style="margin-top:2px">the training method that<br>realigns your posture,<br>increases your mobility<br>and reduces your pain</p>
  </div>

  <div class="abs brand">
    <span class="mark"></span>
    <span class="name">Corvella Motion studio</span>
  </div>

  <h1 class="abs headline">ELIMINATE PAIN &amp;<br><span class="orange">TIGHTNESS</span> <span class="violet">FOR GOOD</span></h1>

  <p class="abs offer">Corvella Motion Studio Offers A Free 60 Minute Seminar:</p>
  <p class="abs guide">"The Busy Walker's Manual for Stretching and Living Lighter."</p>

  <div class="abs cta" style="top:1003px">
    <div class="label">Sign up online at :</div>
    <div class="url">corvellamotionstudio.com/free-seminar</div>
  </div>
  <div class="abs cta-divider"></div>
  <div class="abs cta" style="top:1104px">
    <div class="label">RSVP online at :</div>
    <div class="url">corvellamotionstudio.com</div>
  </div>

  <div class="abs free">FREE</div>
  <div class="abs seminar">SEMINAR</div>
</main>
</body>
</html>
```